Business Card for a Dental Office

The design should communicate integrity, quality and reliability. We also want the card look elegant, simple, but still stand out, different from the traditional-dental-office business card.

Industry/Entity Type

Business

```html
<!DOCTYPE html>
<html lang="en">
<head>
<meta charset="utf-8">
<title>Larkfield Dental Studio — Business Card</title>
<link href="https://fonts.googleapis.com/css2?family=Open+Sans:wght@400;600;700&display=swap" rel="stylesheet">
<style>
  :root {
    --backdrop: #3a3a3c;
    --card-dark: #3b3b3d;
    --card-light: #ffffff;
    --accent: #d9c22a;
    --ink: #1e1e1e;
    --text-light: #ffffff;
  }
  * { margin: 0; padding: 0; box-sizing: border-box; }
  html, body {
    width: 1200px; height: 977px; overflow: hidden;
    background: var(--backdrop);
    font-family: "Open Sans", Arial, sans-serif;
  }
  .canvas { position: relative; width: 1200px; height: 977px; }
  .card {
    position: absolute; left: 75px; top: 188px;
    width: 1050px; height: 600px;
    box-shadow: 0 18px 40px rgba(0,0,0,0.35);
    overflow: hidden;
  }
  .card-bg { position: absolute; inset: 0; }
  .contact-side { position: absolute; left: 92px; top: 150px; color: var(--text-light); }
  .person-name { color: var(--accent); font-weight: 600; font-size: 40px; line-height: 1.1; }
  .person-role { font-weight: 700; font-size: 21px; margin-top: 2px; }
  .details { list-style: none; margin-top: 40px; }
  .details li {
    display: flex; align-items: flex-start; gap: 20px;
    font-size: 21px; line-height: 1.45; margin-bottom: 14px;
  }
  .details .address { margin-bottom: 28px; }
  .details .tight { margin-bottom: 2px; }
  .icon { width: 22px; height: 22px; flex: none; margin-top: 6px; fill: var(--accent); }
  .brand {
    position: absolute; left: 640px; top: 268px;
    display: flex; align-items: center; gap: 14px;
  }
  .brand-square { width: 30px; height: 30px; background: var(--accent); }
  .brand-name {
    color: var(--ink); font-weight: 700; font-size: 34px;
    text-transform: uppercase; letter-spacing: 0.5px;
  }
</style>
</head>
<body>
<main class="canvas">
  <section class="card" aria-label="Business card front">
    <svg class="card-bg" viewBox="0 0 1050 600" width="1050" height="600" aria-hidden="true">
      <rect width="1050" height="600" fill="var(--card-light)"/>
      <rect width="468" height="600" fill="var(--card-dark)"/>
      <polygon points="476,0 481,0 548,600 476,600" fill="var(--accent)"/>
    </svg>

    <div class="contact-side">
      <h1 class="person-name">Daniel Reyes</h1>
      <p class="person-role">Manager</p>
      <ul class="details">
        <li class="address">
          <svg class="icon" viewBox="0 0 24 24"><path d="M12 2a7 7 0 0 0-7 7c0 5 7 13 7 13s7-8 7-13a7 7 0 0 0-7-7zm0 9.5A2.5 2.5 0 1 1 12 6.5a2.5 2.5 0 0 1 0 5z"/></svg>
          <span>4521 Harbor Lane,<br>CA 94110</span>
        </li>
        <li class="tight">
          <svg class="icon" viewBox="0 0 24 24"><path d="M6.6 10.8a15 15 0 0 0 6.6 6.6l2.2-2.2a1 1 0 0 1 1-.25 11.4 11.4 0 0 0 3.6.57 1 1 0 0 1 1 1V20a1 1 0 0 1-1 1A17 17 0 0 1 3 4a1 1 0 0 1 1-1h3.5a1 1 0 0 1 1 1c0 1.25.2 2.45.57 3.57a1 1 0 0 1-.25 1z"/></svg>
          <span>(800) 555-0142</span>
        </li>
        <li class="tight">
          <svg class="icon" viewBox="0 0 24 24"><path d="M2 5h20v14H2z M2 5l10 8 10-8" /></svg>
          <span>hello@larkfield.com</span>
        </li>
        <li class="tight">
          <svg class="icon" viewBox="0 0 24 24"><circle cx="12" cy="12" r="10"/><path d="M2 12h20M12 2c3 3 3 17 0 20M12 2c-3 3-3 17 0 20" stroke="var(--card-dark)" stroke-width="1.5" fill="none"/></svg>
          <span>www.larkfield.com</span>
        </li>
      </ul>
    </div>

    <div class="brand">
      <span class="brand-square" aria-hidden="true"></span>
      <span class="brand-name">Larkfield Dental Studio</span>
    </div>
  </section>
</main>
</body>
</html>
```